PixelMarrow Inc. Website & Mobile Apps Landing Pages

We need a web site design for our company. We develop software and do various consultant projects for our clients. Our products focus on the mobile platform, mainly the Mobile (business, games, social, etc.). We want to communicate that our software is simple and good as candy. The web pages should be fun to look at not loosing seriousness and credibility. Web 2.0 style and 960 grid system a must. We are opened to any overall site colour scheme suggestions (look at the sites we like below).

Must haves:
- Our logo should be seen on the site and look great on it :-) (preview attached below)
- Main home page and app landing page.
- Section links/tabs on the home page (home,apps,support,blog,contact,about)
- No text in images
- Style sheet

Looks we like:
- http://k7q3vxp9lrtwz.examplecdn.net/441_Site_Mock/final_large.jpg
- http://k7q3vxp9lrtwz.examplecdn.net/Deluxe_71_Drawn_Phone_Landing_Page/final.jpg
- http://grenmoor.com/
- http://lumbrel.ca/
- http://fairtwig.com/

Industry/Entity Type

Business

Requirements
Must have
• - Company logo should look great on pages.
• - Main home page and app landing page.
• - Section links/tabs on the home page (home,apps,support,blog,contact,about)
• - Web 2.0 style.
• - 960 grid system (12 col, 16 col).
• - Sliced ann optmized
• - Exported in all major formats (psd,ai,eps,png,jpeg,etc)
• - Style sheet
Should not have
• - Text in images

```html
<!DOCTYPE html>
<html lang="en">
<head>
<meta charset="utf-8">
<title>PixelMarrow Inc.</title>
<link href="https://fonts.googleapis.com/css2?family=Arimo:wght@400;700&display=swap" rel="stylesheet">
<style>
:root{
  --dark:#141414;
  --dark-2:#2a2a2a;
  --page:#e9e9e9;
  --panel:#ffffff;
  --red:#e0201e;
  --ink:#222222;
  --muted:#555555;
  --line:#d8d8d8;
  --teal:#2d5663;
}
*{box-sizing:border-box;margin:0;padding:0}
html,body{width:1101px;height:1200px;overflow:hidden}
body{position:relative;font-family:"Arimo",Arial,sans-serif;color:var(--ink);background:var(--page)}
.abs{position:absolute}
.header{left:0;top:0;width:1101px;height:162px;background:radial-gradient(ellipse at 55% 30%,#3a4a4e 0%,#1c1c1c 45%,#0d0d0d 100%)}
.brand{font-weight:700;color:var(--red);font-size:32px;letter-spacing:.5px;display:flex;align-items:center;gap:10px}
.brand::before{content:"";width:22px;height:22px;border-radius:50%;background:var(--red)}
.header .brand{left:96px;top:30px}
.contact{left:800px;top:32px;color:#fff;font-size:13px;font-weight:700;line-height:18px}
.nav{left:109px;top:97px;width:867px;height:37px;border-radius:4px;background:linear-gradient(#fafafa,#d6d6d6);border:1px solid #bbb;display:flex;align-items:center}
.nav a{height:100%;display:flex;align-items:center;padding:0 23px;font-size:13.5px;color:#333;text-decoration:none;border-right:1px solid #b9b9b9}
.nav a.current{background:linear-gradient(#d9d9d9,#c2c2c2);font-weight:700;padding:0 19px;border-radius:4px 0 0 4px}
.search{left:788px;top:107px;width:172px;height:17px;border:1px solid #aaa;background:#fff;font-size:11.5px;padding-left:4px;line-height:15px;color:#444}
.search svg{position:absolute;right:4px;top:2px}
.slider{left:109px;top:164px;width:867px;height:353px;background:var(--panel)}
.slider h1{left:45px;top:30px;font-weight:400;font-size:46px;line-height:43px;color:var(--red)}
.slider p{left:45px;top:155px;width:515px;font-size:12.5px;line-height:21px;color:#222}
.phone{left:622px;top:-20px;width:170px;height:373px;border-radius:28px 28px 0 0;background:linear-gradient(90deg,#1a1a1a,#3a3a3a 50%,#151515)}
.slide-arrow{width:22px;height:42px;background:#fff;border:1px solid #ccc;top:315px}
.slide-arrow.left{left:87px;border-radius:21px 0 0 21px;border-right:none}
.slide-arrow.right{left:976px;border-radius:0 21px 21px 0;border-left:none}
.slide-arrow svg{position:absolute;top:14px;left:6px}
.dots-bar{left:109px;top:517px;width:867px;height:23px;background:linear-gradient(#f6f6f6,#e2e2e2);display:flex;justify-content:center;align-items:center;gap:5px}
.dots-bar span{width:14px;height:14px;border-radius:50%;background:#f0f0f0;border:1px solid #bbb}
.dots-bar span.on{background:var(--teal);border-color:var(--teal)}
.shelf{left:120px;top:540px;width:845px;height:14px;border-radius:50%;background:radial-gradient(ellipse at center,rgba(0,0,0,.75),rgba(0,0,0,0) 70%)}
.content{left:109px;top:585px;width:654px;height:483px;background:var(--panel)}
.content h2{font-weight:400;font-size:21px;color:#222;position:absolute;left:7px}
.intro{left:7px;top:39px;width:640px;font-size:11.5px;line-height:16.5px;color:var(--muted)}
.divider{left:7px;top:124px;width:640px;height:1px;background:var(--line)}
.app{width:310px;height:72px}
.app .icon{left:0;top:0;width:48px;height:48px;border-radius:6px}
.app h3{left:56px;top:0;font-size:12px;font-weight:400;color:#111}
.app p{left:56px;top:17px;width:228px;font-size:10.5px;line-height:13px;color:var(--muted)}
.more{right:18px;top:43px;background:#111;color:#fff;font-size:9px;padding:1px 5px;border-radius:6px}
.row-line{height:1px;background:var(--line);width:640px;left:7px}
.side{left:773px;width:198px;border:1px solid #c9c9c9;border-radius:4px;background:linear-gradient(#fbfbfb,#e7e7e7)}
.side h4{position:absolute;left:11px;font-size:12.5px;font-weight:700;color:#111;line-height:15px}
.side p{position:absolute;left:11px;font-size:10.5px;line-height:13px;color:#222}
.side .art{position:absolute;border-radius:6px}
.footer{left:0;top:1080px;width:1101px;height:120px;background:linear-gradient(#2b2b2b,#121212)}
.footer .brand{left:120px;top:40px}
.social{left:773px;top:26px;display:flex;gap:15px}
.social span{width:26px;height:26px;border-radius:4px;background:#4a6fa5}
.copyright{right:132px;top:100px;font-size:10.5px;color:#aaa}
</style>
</head>
<body>
<header class="header abs">
  <div class="brand abs">PixelMarrow</div>
  <div class="contact abs">Call Us: 123-123-123<br>Email:info@pixelmarrow.com</div>
</header>
<nav class="nav abs">
  <a class="current" href="#">Home</a><a href="#">Portfolio</a><a href="#">Blog</a><a href="#">Services</a><a href="#">About Us</a><a href="#">Contact Us</a>
</nav>
<div class="search abs">search...
  <svg width="12" height="12" viewBox="0 0 12 12"><circle cx="5" cy="5" r="3.5" fill="none" stroke="#888" stroke-width="1.4"/><line x1="7.5" y1="7.5" x2="11" y2="11" stroke="#888" stroke-width="1.6"/></svg>
</div>

<section class="slider abs">
  <h1 class="abs">Stylish applications<br>Now in Your hand!</h1>
  <p class="abs">It is a long established fact that a reader will be distracted by the readable content of a page when looking at its layout. The point of using Lorem Ipsum is that it has a more-or-less normal distribution of letters, as opposed to using 'Content here, content here', making it look like readable English. as opposed to using 'Content here, content here', making it look like readable English.</p>
  <div class="phone abs" role="img" aria-label="Photo of a smartphone showing its home screen of app icons"></div>
</section>
<div class="slide-arrow left abs"><svg width="10" height="14"><path d="M8 2 3 7l5 5" fill="none" stroke="#2d5663" stroke-width="2.4"/></svg></div>
<div class="slide-arrow right abs"><svg width="10" height="14"><path d="M2 2l5 5-5 5" fill="none" stroke="#2d5663" stroke-width="2.4"/></svg></div>
<div class="dots-bar abs"><span></span><span class="on"></span><span></span><span></span><span></span><span></span></div>
<div class="shelf abs"></div>

<main class="content abs">
  <h2 style="top:8px">Welcome to Our Site</h2>
  <p class="intro abs">It is a long established fact that a reader will be distracted by the readable content of a page when looking at its layout. The point of using Lorem Ipsum is that it has a more-or-less normal distribution of letters, as opposed to using 'Content here, content here', making it look like readable English.It is a long established fact that a reader will be distracted by the readable content of a page when looking at its layout. The point of using Lorem Ipsum is that it has a more-or-less normal distribution of letters, as opposed to using 'Content here,</p>
  <div class="divider abs"></div>
  <h2 style="top:134px">Applications</h2>

  <div class="app abs" style="left:11px;top:168px"><div class="icon abs" style="background:#3a1a08" role="img" aria-label="Halloween puzzle app icon"></div><h3 class="abs">Halloween pics puzzles</h3><p class="abs">10/21/2010 Halloween coming soon! Enjoy this sliding puzzle with multiple scary pictures.</p><span class="more abs">read more</span></div>
  <div class="app abs" style="left:332px;top:171px"><div class="icon abs" style="background:#4d7fb0" role="img" aria-label="Calendar app icon"></div><h3 class="abs">Halloween pics puzzles</h3><p class="abs">10/21/2010 Halloween coming soon! Enjoy this sliding puzzle with multiple scary pictures.</p><span class="more abs">read more</span></div>
  <div class="row-line abs" style="top:238px"></div>
  <div class="app abs" style="left:11px;top:255px"><div class="icon abs" style="background:#3f7fd0" role="img" aria-label="Camera app icon"></div><h3 class="abs">Halloween pics puzzles</h3><p class="abs">10/21/2010 Halloween coming soon! Enjoy this sliding puzzle with multiple scary pictures.</p><span class="more abs">read more</span></div>
  <div class="app abs" style="left:332px;top:257px"><div class="icon abs" style="background:#c0463a" role="img" aria-label="Tic tac toe game icon"></div><h3 class="abs">Halloween pics puzzles</h3><p class="abs">10/21/2010 Halloween coming soon! Enjoy this sliding puzzle with multiple scary pictures.</p><span class="more abs">read more</span></div>
  <div class="row-line abs" style="top:324px"></div>
  <div class="app abs" style="left:11px;top:340px"><div class="icon abs" style="background:#d9c25a" role="img" aria-label="Tic tac toe game icon"></div><h3 class="abs">Halloween pics puzzles</h3><p class="abs">10/21/2010 Halloween coming soon! Enjoy this sliding puzzle with multiple scary pictures.</p><span class="more abs">read more</span></div>
  <div class="app abs" style="left:332px;top:336px"><div class="icon abs" style="background:#3f7c3a" role="img" aria-label="Football game icon"></div><h3 class="abs">Halloween pics puzzles</h3><p class="abs">10/21/2010 Halloween coming soon! Enjoy this sliding puzzle with multiple scary pictures.</p><span class="more abs">read more</span></div>
  <div class="row-line abs" style="top:402px"></div>
  <div class="app abs" style="left:11px;top:413px"><div class="icon abs" style="background:#7cbf3a" role="img" aria-label="Green app icon"></div><h3 class="abs">Halloween pics puzzles</h3><p class="abs">10/21/2010 Halloween coming soon! Enjoy this sliding puzzle with multiple scary pictures.</p><span class="more abs">read more</span></div>
  <div class="app abs" style="left:332px;top:413px"><div class="icon abs" style="background:#5a1410" role="img" aria-label="Skull pattern game icon"></div><h3 class="abs">Halloween pics puzzles</h3><p class="abs">10/21/2010 Halloween coming soon! Enjoy this sliding puzzle with multiple scary pictures.</p><span class="more abs">read more</span></div>
</main>

<aside>
  <div class="side abs" style="top:593px;height:176px">
    <div class="art" style="left:10px;top:12px;width:176px;height:82px;background:linear-gradient(#444,#1a1a1a)" role="img" aria-label="Four smartphones showing web apps"></div>
    <h4 style="top:114px">What are web apps?</h4>
    <p style="top:135px">Learn what are they are and how<br>to use them. ▸</p>
  </div>
  <div class="side abs" style="top:783px;height:93px">
    <h4 style="top:13px">Web<br>Development<br>for Mobile</h4>
    <p style="top:69px">Here's how to creat your own. ▸</p>
    <div class="art" style="left:126px;top:8px;width:58px;height:52px;background:linear-gradient(#a7c3dc,#5b7f9f)" role="img" aria-label="Book illustration"></div>
  </div>
  <div class="side abs" style="top:892px;height:77px">
    <h4 style="top:10px">Submitting<br>Applications</h4>
    <p style="top:43px">How to submit your web<br>app. ▸</p>
    <div class="art" style="left:139px;top:10px;width:48px;height:48px;background:linear-gradient(#8fd0f7,#1f6fd1)" role="img" aria-label="Compass app icon"></div>
  </div>
  <div class="side abs" style="top:984px;height:77px">
    <h4 style="top:9px">Feedback</h4>
    <p style="top:29px">Help us improve our<br>web apps library. ▸</p>
    <div class="art" style="left:139px;top:10px;width:48px;height:52px;background:linear-gradient(#fafafa,#bdbdbd)" role="img" aria-label="Paper and pen illustration"></div>
  </div>
</aside>

<footer class="footer abs">
  <div class="brand abs">PixelMarrow</div>
  <div class="social abs"><span></span><span style="background:#3fa7d6"></span><span style="background:#e46b1c"></span><span style="background:#2a6d9c"></span><span style="background:#444"></span></div>
  <div class="copyright abs">Copyright © 2010 PixelMarrow. All Rights reserved</div>
</footer>
</body>
</html>
```